Luxury Tours Design

We are “Amber Coachline” a Chauffeur Company based in Maidenhead, Berkshire. Our website is - ambercoachline.co.uk which will give you an insite into the Company.
Our clients consist of luxurious Hotels, large Corporate Companies along with private UHNW clients.
We have a fleet of Valtrane E, S and V Class vehicles along with 16 Seater Executive Coaches so we can accommodate single travellers, couples, friends, families and groups.
We would like an A5 (or slightly larger) double sided colour leaflet designed to promote our Tours in our local and surrounding areas.
The information below is some indication as to what we would like.
On the front we would like:-
Amber Coachline “Signature Tour” This will be our main promoting Tour
Slogan “Amber Coachline….ever at your service”
Tour will include:-
Visiting the historic town of Windsor, Hollenby Castle, St Aldric’s Chapel and Regal Pemberly Shopping Arcade.
Then onto Eton (Dunmere College) and a lovely view of the River Thames along with an array of Antique Shops in the quaint streets.
Bray Village (Heron Isle), renowed for it’s Brevard Star Restaurants and pubs.
Through picturesque Cookham along to Marlow for some shopping in the boutique shops, small listed buildings and beautiful places for refreshments, along with stunning views of the River Thames form Ashcombe Bridge.
This will be our main tour we offer but again this is flexible. This aims to be around 4-5 hours.
On the front, a picture of Hollenby castle maybe a large picture with writing over the top, or a separate photo….. a couple of photos attached or something similar.
On the back of the leaflet:-
We offer London based tours including:-
Belvards, Larkmoor Park, Ravensholt Palace, Corringdale Palace, Pellington Square, Turning of the Sentries, Keep of Ardmoor, Tall Tom, Glenmoreton Abbey to name a few! Or maybe London by night with a show or restaurant.
On the back a picture of Corringdale Palace…a couple of picture are also attached or again something similar.
Other Tours provided:-
Ridgewell Court Palace, Oxford and Corvane Palace, Ashmarrow Ring and Bath, The Cotswolds, Stratford and Penlow Castle, Quillford Shopping Village.
Also bespoke Tours can be arranged. We can personalise any tour to your requirements.
Experienced friendly Chauffeur’s, no request too big or small.
Please call us on 01632 960417 or email us sales@ambercoachline.co.uk
Please can you do an initial design including the above information.
Look forward to hearing from you.
Kind regards
Please visit https://www.hartleyprivatedrives.co.uk/ to get an idea of the tours of London to go on the back.
Prices will follow to be added after design and layout has been done.
Our AC logo is available on www.ambercoachline.co.uk
We want text to be editable and also for the design to have a luxury feel.
Chauffeur

```html
<!DOCTYPE html>
<html lang="en">
<head>
<meta charset="utf-8">
<title>Amber Coachline – Tours Leaflet</title>
<link rel="stylesheet" href="https://fonts.googleapis.com/css2?family=Great+Vibes&family=Poppins:ital,wght@0,400;0,500;0,600;1,400;1,600&display=swap">
<style>
  :root {
    --canvas: #ffffff;
    --ink: #1f1d1a;
    --dark: #25231f;
    --panel: rgba(107, 99, 70, 0.88);
    --gold: #d9b94a;
    --gold-soft: #e6cf7a;
    --title-brown: #4a4330;
    --white: #ffffff;
    --sky-top: #b9cfe0;
    --sky-mid: #f0c2b6;
    --sky-pink: #f39a8f;
  }
  * { margin: 0; padding: 0; box-sizing: border-box; }
  html, body { width: 800px; height: 1200px; overflow: hidden; background: var(--canvas); }
  body { position: relative; font-family: "Poppins", sans-serif; color: var(--ink); }

  .leaflet { position: absolute; left: 213px; width: 374px; height: 529px; overflow: hidden; background: var(--dark); }
  .leaflet--london { top: 55px; }
  .leaflet--signature { top: 636px; }
  .abs { position: absolute; }

  .scene { position: absolute; left: 0; top: 0; width: 100%; }
  .scene--palace {
    height: 330px;
    background: linear-gradient(180deg, var(--sky-top) 0%, #e7dcd8 22%, var(--sky-mid) 38%, var(--sky-pink) 52%, #cfc9c0 60%, #b9b3a8 70%, #c7a83a 80%, #c8352d 88%, #d8c640 96%, var(--dark) 100%);
  }
  .scene--castle {
    height: 290px;
    background: linear-gradient(180deg, #c9d3dc 0%, #e9c9c0 18%, #f2a792 30%, #8e8a77 40%, #4f6a32 52%, #3f5f28 72%, #2f3b24 88%, var(--dark) 100%);
  }

  .script { font-family: "Great Vibes", cursive; font-weight: 400; white-space: nowrap; }
  .center { left: 0; width: 100%; text-align: center; }

  .london-title { top: 14px; font-size: 36px; color: var(--ink); }
  .sights { font-size: 8px; line-height: 14.3px; color: var(--ink); list-style: none; }
  .night-line { top: 112px; left: 34px; font-size: 8px; font-weight: 600; font-style: italic; }

  .panel { position: absolute; background: var(--panel); }
  .panel--other { left: 36px; top: 313px; width: 302px; height: 138px; }
  .other-title { top: 6px; font-size: 24px; color: var(--gold); }
  .other-list { list-style: none; font-size: 7px; letter-spacing: 0.1px; line-height: 14.3px; color: var(--white); text-transform: uppercase; }
  .quote { font-style: italic; color: var(--gold); text-align: center; }
  .quote-mark { font-family: Georgia, serif; font-style: normal; font-weight: 700; color: var(--gold); }
  .panel--other .quote { top: 95px; left: 16px; width: 270px; font-size: 7px; line-height: 9px; }
  .prices { top: 122px; font-size: 8px; color: var(--gold-soft); }

  .contact-label { font-size: 6px; letter-spacing: 1.2px; color: var(--gold); text-transform: uppercase; }
  .contact-row { display: flex; justify-content: center; align-items: center; gap: 9px; font-size: 6px; color: var(--white); font-weight: 500; }
  .contact-row .item { display: flex; align-items: center; gap: 3px; }
  .contact-row .phone { font-size: 7.5px; font-weight: 600; }
  .contact-row .sep { width: 1px; height: 8px; background: #8a8470; }
  .contact-row svg { width: 9px; height: 9px; }

  .brand { display: flex; justify-content: center; align-items: center; gap: 6px; }
  .brand-mark { width: 16px; height: 16px; border-radius: 50%; background: #8f8a80; }
  .brand-name { font-size: 11px; color: var(--white); font-weight: 500; }

  .signature-title { top: 14px; font-size: 50px; color: var(--title-brown); }
  .slogan { top: 64px; font-size: 21px; color: var(--ink); }
  .fleet { top: 236px; left: 20px; width: 334px; font-size: 9px; line-height: 11px; color: var(--white); text-align: center; }

  .panel--windsor { left: 44px; top: 291px; width: 286px; height: 161px; }
  .windsor-heading { left: 11px; top: 4px; font-size: 12px; line-height: 12.5px; color: var(--gold); font-weight: 500; text-transform: uppercase; }
  .price-badge { left: 232px; top: 9px; width: 45px; height: 15px; background: #a08c3e; color: var(--white); }
  .price-badge .from { position: absolute; left: 6px; top: 1px; font-size: 3px; }
  .price-badge .amount { position: absolute; left: 6px; top: 3px; font-size: 8.5px; font-weight: 600; }
  .itinerary p { position: absolute; left: 11px; width: 262px; font-size: 6px; line-height: 7.5px; color: var(--white); }
  .panel--windsor .quote { top: 137px; font-size: 8px; }
</style>
</head>
<body>

<!-- Back side: London tours -->
<section class="leaflet leaflet--london">
  <div class="scene scene--palace" role="img" aria-label="Photograph of Corringdale Palace at sunset with beds of red and yellow tulips in front"></div>

  <h1 class="abs center script london-title">London Tours</h1>

  <ul class="abs sights" style="left:34px; top:59px;">
    <li>Belvards</li><li>Larkmoor Park</li><li>Ravensholt Palace</li>
  </ul>
  <ul class="abs sights" style="left:135px; top:59px;">
    <li>Corringdale Palace</li><li>Pellington Square</li><li>Turning of the Sentries</li>
  </ul>
  <ul class="abs sights" style="left:261px; top:57px;">
    <li>Keep of Ardmoor</li><li>Tall Tom</li><li>Glenmoreton Abbey</li>
  </ul>

  <p class="abs night-line">Or maybe London by night with a show or restaurant.</p>

  <div class="panel panel--other">
    <h2 class="abs center script other-title">Other Tours Available</h2>
    <ul class="abs other-list" style="left:24px; top:43px;">
      <li>Ridgewell Court Palace</li><li>Oxford and Corvane Palace</li><li>Ashmarrow Ring and Bath</li>
    </ul>
    <ul class="abs other-list" style="left:162px; top:43px;">
      <li>The Cotswolds</li><li>Stratford and Penlow Castle</li><li>Quillford Shopping Village</li>
    </ul>
    <p class="abs quote"><span class="quote-mark">“</span> Also bespoke tours can be arranged. We can personalize any tour to your requirements with our friendly, experienced chauffeurs <span class="quote-mark">”</span></p>
    <p class="abs center prices">Prices On Request</p>
  </div>

  <p class="abs center contact-label" style="top:460px;">Contact Us</p>
  <div class="abs center contact-row" style="top:474px;">
    <span class="item"><svg viewBox="0 0 10 10"><circle cx="5" cy="5" r="4.4" fill="none" stroke="#d9b94a" stroke-width=".7"/><rect x="2.8" y="3.5" width="4.4" height="3" fill="none" stroke="#d9b94a" stroke-width=".6"/><path d="M2.8 3.5 L5 5.2 L7.2 3.5" fill="none" stroke="#d9b94a" stroke-width=".6"/></svg>sales@ambercoachline.co.uk</span>
    <span class="sep"></span>
    <span class="item phone"><svg viewBox="0 0 10 10"><circle cx="5" cy="5" r="4.4" fill="none" stroke="#d9b94a" stroke-width=".7"/><path d="M3.3 2.9 C3 4.8 4.8 6.9 6.9 6.8 L7 6 L6 5.5 L5.6 6 C4.9 5.7 4.3 5 4.1 4.4 L4.6 4 L4.1 3 Z" fill="none" stroke="#d9b94a" stroke-width=".5"/></svg>01632 960417</span>
    <span class="sep"></span>
    <span class="item"><svg viewBox="0 0 10 10"><circle cx="5" cy="5" r="4.4" fill="none" stroke="#d9b94a" stroke-width=".7"/><circle cx="5" cy="5" r="2.5" fill="none" stroke="#d9b94a" stroke-width=".5"/><path d="M2.5 5 H7.5 M5 2.5 C4 4 4 6 5 7.5 M5 2.5 C6 4 6 6 5 7.5" fill="none" stroke="#d9b94a" stroke-width=".4"/></svg>www.ambercoachline.co.uk</span>
  </div>
  <div class="abs center brand" style="top:495px;">
    <span class="brand-mark"></span><span class="brand-name">Amber Coachline</span>
  </div>
</section>

<!-- Front side: Signature tour -->
<section class="leaflet leaflet--signature">
  <div class="scene scene--castle" role="img" aria-label="Photograph of Hollenby Castle at the end of a long tree-lined avenue under a pink evening sky"></div>

  <h1 class="abs center script signature-title">Signature Tour</h1>
  <p class="abs center script slogan">Amber Coachline….ever at your service</p>

  <p class="abs fleet">We have a fleet of Valtrane E, S and V Class vehicles along with 16 Seater Executive Coaches so we can accommodate single travellers, couples, friends, families and groups.</p>

  <div class="panel panel--windsor">
    <h2 class="abs windsor-heading">Visit to the historic<br>town of Windsor</h2>
    <div class="abs price-badge"><span class="from">FROM</span><span class="amount">£350.00</span></div>
    <div class="itinerary">
      <p style="top:43px;">Visiting the historic town of Windsor, Hollenby Castle, St Aldric’s Chapel and Regal Pemberly Shopping Arcade.</p>
      <p style="top:66px;">Eton and Dunmere College with lovely views of the River Thames along with an array of Antique Shops in the quaint streets.</p>
      <p style="top:88px;">Bray Village renowned for it’s Brevard Star restaurants and pubs, along with a visit to Heron Isle.</p>
      <p style="top:110px;">Through picturesque Cookham along to Marlow for some shopping in the boutique shops, small listed buildings and beautiful places for refreshments, along with stunning views of the River Thames from Ashcombe Bridge.</p>
    </div>
    <p class="abs center quote"><span class="quote-mark">“</span>Our signature tour is approximately 4 hours<span class="quote-mark">”</span></p>
  </div>

  <p class="abs center contact-label" style="top:460px;">Contact Us</p>
  <div class="abs center contact-row" style="top:474px;">
    <span class="item"><svg viewBox="0 0 10 10"><circle cx="5" cy="5" r="4.4" fill="none" stroke="#d9b94a" stroke-width=".7"/><rect x="2.8" y="3.5" width="4.4" height="3" fill="none" stroke="#d9b94a" stroke-width=".6"/><path d="M2.8 3.5 L5 5.2 L7.2 3.5" fill="none" stroke="#d9b94a" stroke-width=".6"/></svg>sales@ambercoachline.co.uk</span>
    <span class="sep"></span>
    <span class="item phone"><svg viewBox="0 0 10 10"><circle cx="5" cy="5" r="4.4" fill="none" stroke="#d9b94a" stroke-width=".7"/><path d="M3.3 2.9 C3 4.8 4.8 6.9 6.9 6.8 L7 6 L6 5.5 L5.6 6 C4.9 5.7 4.3 5 4.1 4.4 L4.6 4 L4.1 3 Z" fill="none" stroke="#d9b94a" stroke-width=".5"/></svg>01632 960417</span>
    <span class="sep"></span>
    <span class="item"><svg viewBox="0 0 10 10"><circle cx="5" cy="5" r="4.4" fill="none" stroke="#d9b94a" stroke-width=".7"/><circle cx="5" cy="5" r="2.5" fill="none" stroke="#d9b94a" stroke-width=".5"/><path d="M2.5 5 H7.5 M5 2.5 C4 4 4 6 5 7.5 M5 2.5 C6 4 6 6 5 7.5" fill="none" stroke="#d9b94a" stroke-width=".4"/></svg>www.ambercoachline.co.uk</span>
  </div>
  <div class="abs center brand" style="top:499px;">
    <span class="brand-mark"></span><span class="brand-name">Amber Coachline</span>
  </div>
</section>

</body>
</html>
```